Need Help having my business card stand out

I am the owner of Birchway Canine Training and would like for my business cards to stand out. I have been trying to keep designing them myself but I can't get what I have in my head on the card. I will try my best to post templates that I like for inspirations. I want something unique but elegant. I don't want in to look cartoony or cheesy. It needs to pop in a pet shop but also in a coffee shop or gym.

Target Market(s)

Dog owners, Married ,No young kids Jr High school kids and up (maybe kids on the way) Executives, Stay at home moms/wives, Small business owners

Industry/Entity Type

Dog Training

Contact Information for Business Card

Lowell Spratt, 281-904-3376, info@birchwaycanine.example, www.birchwaycanine.example

Colors

Designer to choose colors to be used in the design.

Requirements
Must have
• my logo
Should not have
• Cursive lettering

```html
<!DOCTYPE html>
<html lang="en">
<head>
<meta charset="utf-8">
<title>Birchway Canine Training – Business Card</title>
<link href="https://fonts.googleapis.com/css2?family=Archivo:wght@400;600;700&display=swap" rel="stylesheet">
<style>
  :root {
    --bg: #b4b5b9;
    --paper: #ffffff;
    --ink: #000000;
    --ink-soft: #ffffff;
  }
  * { margin: 0; padding: 0; box-sizing: border-box; }
  html, body {
    width: 1200px; height: 1178px; overflow: hidden;
    background: var(--bg);
    font-family: "Archivo", Arial, sans-serif;
  }
  .card {
    position: absolute;
    top: 458px;
    width: 496px; height: 284px;
    background: var(--paper);
  }
  .card--front { left: 66px; }
  .card--back { left: 628px; }

  .card__logo-zone {
    position: absolute; left: 0; top: 0;
    width: 248px; height: 100%;
    display: flex; align-items: center; justify-content: center;
  }
  .brand-name {
    color: var(--ink);
    font-weight: 700;
    text-transform: uppercase;
    text-align: center;
    line-height: 1.1;
  }
  .card__logo-zone .brand-name { font-size: 21px; letter-spacing: 0.5px; }

  .card__details {
    position: absolute; left: 248px; top: 0;
    width: 248px; height: 100%;
    background: var(--ink);
    color: var(--ink-soft);
    padding: 70px 0 0 39px;
  }
  .person__name { font-size: 17px; font-weight: 600; letter-spacing: 0.3px; }
  .person__role { font-size: 12px; font-weight: 600; margin-top: 1px; }
  .contact-list { list-style: none; margin-top: 48px; }
  .contact-list li {
    display: flex; align-items: center; gap: 8px;
    font-size: 12.5px; line-height: 20px; font-weight: 400;
  }
  .contact-list svg { width: 11px; height: 11px; flex: none; }

  .card--back {
    display: flex; flex-direction: column; align-items: center; justify-content: center;
  }
  .card--back .brand-name { font-size: 34px; letter-spacing: 1px; }
</style>
</head>
<body>
  <section class="card card--front">
    <div class="card__logo-zone">
      <p class="brand-name">Birchway<br>Canine Training</p>
    </div>
    <div class="card__details">
      <p class="person__name">LOWELL SPRATT</p>
      <p class="person__role">Founder &amp; CEO</p>
      <ul class="contact-list">
        <li>
          <svg viewBox="0 0 12 12" aria-hidden="true"><path d="M3 1l2 2.5-1.2 1.2c.6 1.4 1.6 2.4 3 3L8 6.5 10.5 8.5 9.3 10.5C5.5 10 2 6.5 1.5 2.7z" fill="currentColor"/></svg>
          <span>281-904-3376</span>
        </li>
        <li>
          <svg viewBox="0 0 12 12" aria-hidden="true"><circle cx="6" cy="6" r="2" fill="none" stroke="currentColor" stroke-width="1.3"/><path d="M8 4v3c0 1.2 2 1.2 2-.5A4 4 0 1 0 8 9.6" fill="none" stroke="currentColor" stroke-width="1.3"/></svg>
          <span>info@birchwaycanine.example</span>
        </li>
        <li>
          <svg viewBox="0 0 12 12" aria-hidden="true"><g fill="none" stroke="currentColor" stroke-width="1"><circle cx="6" cy="6" r="5"/><ellipse cx="6" cy="6" rx="2.2" ry="5"/><path d="M1 6h10M2 3.5h8M2 8.5h8"/></g></svg>
          <span>www.birchwaycanine.example</span>
        </li>
      </ul>
    </div>
  </section>

  <section class="card card--back">
    <p class="brand-name">Birchway<br>Canine Training</p>
  </section>
</body>
</html>
```